Business Card For Halvenmoor Financial Consulting

Hi, I would like a business card designed. Bold, modern.
Please use the same design as the logo. I have also attached the website design to see the overall theme.
Wordmark Font
Color: Hex: #01AEF7

```html
<!DOCTYPE html>
<html lang="en">
<head>
<meta charset="utf-8">
<title>Halvenmoor Consulting – Business Card</title>
<link href="https://fonts.googleapis.com/css2?family=Josefin+Sans:wght@400;600;700&display=swap" rel="stylesheet">
<style>
  :root {
    --brand-blue: #01AEF7;
    --steel-blue: #2a9bd2;
    --steel-deep: #14648f;
    --card-dark: #14202a;
    --card-darker: #0f1920;
    --panel-faint: #1a2d3a;
    --text-light: #f2f4f6;
    --page-bg: #2b2d30;
  }
  * { margin: 0; padding: 0; box-sizing: border-box; }
  html, body { width: 1200px; height: 900px; overflow: hidden; }
  body {
    background: var(--page-bg);
    font-family: "Josefin Sans", sans-serif;
    display: flex; align-items: center; justify-content: center; gap: 40px;
  }
  .card {
    width: 540px; height: 309px; position: relative; overflow: hidden;
    flex-shrink: 0;
    box-shadow: 0 12px 30px rgba(0,0,0,.45);
  }
  /* Front */
  .card-front {
    background: linear-gradient(100deg, var(--steel-deep) 0%, var(--steel-blue) 22%, #1c7fb5 40%, #34a6dd 62%, #1e86bd 80%, var(--steel-blue) 100%);
    display: flex; align-items: center; justify-content: center; gap: 12px;
  }
  .front-name {
    color: var(--text-light); font-weight: 700; font-size: 30px; letter-spacing: 2px;
  }
  .front-mark { width: 18px; height: 18px; background: var(--text-light); }
  /* Back */
  .card-back { background: var(--card-dark); }
  .back-decor {
    position: absolute; left: 14px; top: 70px; width: 150px; height: 150px;
    background: var(--panel-faint);
  }
  .wordmark { position: absolute; left: 190px; top: 42px; display: flex; align-items: center; gap: 12px; }
  .wordmark-square { width: 40px; height: 40px; background: var(--brand-blue); }
  .wordmark-name { color: var(--text-light); font-weight: 700; font-size: 34px; letter-spacing: 1px; line-height: 1; }
  .wordmark-tag { color: var(--brand-blue); font-weight: 700; font-size: 11px; letter-spacing: 13px; margin-top: 4px; }
  .rule-top { position: absolute; left: 200px; right: 28px; top: 132px; height: 1px; background: var(--brand-blue); }
  .person { position: absolute; left: 100px; top: 176px; font-size: 17px; color: var(--text-light); }
  .person-name { color: var(--brand-blue); font-weight: 700; letter-spacing: 1px; }
  .person-sep { color: var(--brand-blue); margin: 0 6px; }
  .rule-bottom { position: absolute; left: 100px; right: 28px; top: 200px; height: 1px; background: var(--brand-blue); }
  .contacts { position: absolute; left: 104px; top: 210px; right: 24px; font-size: 11.5px; color: var(--text-light); line-height: 22px; }
  .contact-row { display: flex; align-items: center; white-space: nowrap; }
  .contact-item { display: inline-flex; align-items: center; gap: 5px; }
  .contact-sep { color: var(--brand-blue); margin: 0 6px; }
  .icon { width: 11px; height: 11px; fill: var(--brand-blue); flex-shrink: 0; }
  .band-dark { position: absolute; left: 0; right: 0; bottom: 16px; height: 6px; background: var(--card-darker); }
  .band-blue {
    position: absolute; left: 0; right: 0; bottom: 0; height: 16px;
    background: linear-gradient(90deg, var(--steel-deep), var(--steel-blue) 40%, #4bb8ea 60%, var(--steel-deep));
  }
</style>
</head>
<body>
  <section class="card card-front" aria-label="Business card front">
    <span class="front-mark"></span>
    <span class="front-name">HALVENMOOR</span>
  </section>

  <section class="card card-back" aria-label="Business card back">
    <div class="back-decor"></div>
    <div class="wordmark">
      <span class="wordmark-square"></span>
      <div>
        <div class="wordmark-name">HALVENMOOR</div>
        <div class="wordmark-tag">CONSULTING</div>
      </div>
    </div>
    <div class="rule-top"></div>
    <p class="person"><span class="person-name">MARCUS HALE</span><span class="person-sep">|</span>Manager</p>
    <div class="rule-bottom"></div>
    <div class="contacts">
      <div class="contact-row">
        <span class="contact-item">
          <svg class="icon" viewBox="0 0 24 24"><path d="M6.6 10.8a15.1 15.1 0 0 0 6.6 6.6l2.2-2.2a1 1 0 0 1 1-.25 11.4 11.4 0 0 0 3.6.57 1 1 0 0 1 1 1V20a1 1 0 0 1-1 1A17 17 0 0 1 3 4a1 1 0 0 1 1-1h3.5a1 1 0 0 1 1 1c0 1.250.2 2.450.57 3.570a1 1 0 0 1-.25 1z"/></svg>
          (025) 481 30572</span>
        <span class="contact-sep">|</span>
        <span class="contact-item">
          <svg class="icon" viewBox="0 0 24 24"><path d="M12 2a10 10 0 1 0 0 20 10 10 0 0 0 0-20zm6.9 6h-3a15.6 15.6 0 0 0-1.4-3.6A8 8 0 0 1 18.9 8zM12 4c.8 1.2 1.5 2.5 1.9 4h-3.8c.4-1.5 1.1-2.8 1.9-4zM4.3 14a8 8 0 0 1 0-4h3.4a16 16 0 0 0 0 4zm.8 2h3a15.6 15.6 0 0 0 1.4 3.6A8 8 0 0 1 5.1 16zm3-8h-3a8 8 0 0 1 4.4-3.6A15.6 15.6 0 0 0 8.1 8zM12 20c-.8-1.2-1.5-2.5-1.9-4h3.8c-.4 1.5-1.1 2.8-1.9 4zm2.3-6H9.7a14.7 14.7 0 0 1 0-4h4.6a14.7 14.7 0 0 1 0 4zm.2 5.6a15.6 15.6 0 0 0 1.4-3.6h3a8 8 0 0 1-4.4 3.6zm1.8-5.6a16 16 0 0 0 0-4h3.4a8 8 0 0 1 0 4z"/></svg>
          www.halvenmoorconsulting.com</span>
      </div>
      <div class="contact-row">
        <span class="contact-item">
          <svg class="icon" viewBox="0 0 24 24"><path d="M3 5h18a1 1 0 0 1 1 1v12a1 1 0 0 1-1 1H3a1 1 0 0 1-1-1V6a1 1 0 0 1 1-1zm9 7.5L4 7.3V17h16V7.3z"/></svg>
          hello@halvenmoor.org</span>
        <span class="contact-sep">|</span>
        <span class="contact-item">
          <svg class="icon" viewBox="0 0 24 24"><path d="M12 2a7 7 0 0 0-7 7c0 5.2 7 13 7 13s7-7.8 7-13a7 7 0 0 0-7-7zm0 9.5A2.5 2.5 0 1 1 12 6.5a2.5 2.5 0 0 1 0 5z"/></svg>
          2718 Larkspur Avenue, Ridgefield, FL 79240</span>
      </div>
    </div>
    <div class="band-dark"></div>
    <div class="band-blue"></div>
  </section>
</body>
</html>
```